Pet Sitting Business Card

Would like a business card designed for my new pet sitting business
Card needs to match with logo design.
Blue and Orange are the theme colours.

Simple yet sophisticated design

company name:- MEADOWLARK PET CARE
Dana Kovich
Owner
0452716093
dana@meadowlarkpetcare.com.au
www.meadowlarkpetcare.com.au

I'm going to close my deadline early. I will be picking a winner by the 10th of May. Please submit designs before then.
thank you

Target Market(s)

All types of professional pet lovers wishing to have their pet looked after

Industry/Entity Type

Pet

Requirements
Must have
• Logo design
Blue and orange

```html
<!DOCTYPE html>
<html lang="en">
<head>
<meta charset="utf-8">
<title>Meadowlark Pet Care – Business Card</title>
<link href="https://fonts.googleapis.com/css2?family=Michroma&display=swap" rel="stylesheet">
<style>
  :root {
    --stage: #2b2b2b;
    --card: #eeeff0;
    --blue: #2b97ec;
    --blue-light: #63c7f5;
    --orange: #ec8a26;
    --ink: #3b3b3b;
    --white: #ffffff;
  }
  * { margin: 0; padding: 0; box-sizing: border-box; }
  html, body { width: 1200px; height: 900px; overflow: hidden; }
  body {
    background: var(--stage);
    font-family: "Michroma", "Arial", sans-serif;
    position: relative;
  }
  .card {
    position: absolute;
    width: 620px;
    height: 354px;
    border-radius: 26px;
    background: var(--card);
    overflow: hidden;
    box-shadow: 0 18px 40px rgba(0,0,0,.45);
  }
  .card-front { left: 80px; top: 70px; }
  .card-back { left: 500px; top: 476px; }
  .card-art { position: absolute; inset: 0; }

  .website {
    position: absolute;
    left: 42px; top: 40px;
    color: var(--white);
    font-size: 14px;
    letter-spacing: .5px;
  }
  .brand {
    position: absolute;
    display: flex;
    align-items: center;
    gap: 12px;
  }
  .brand-dot {
    width: 22px; height: 22px;
    border-radius: 50%;
    background: var(--orange);
    flex: none;
  }
  .brand-name {
    color: var(--blue);
    font-size: 22px;
    line-height: 1.25;
    letter-spacing: 1px;
  }
  .card-front .brand { left: 250px; top: 190px; }
  .card-back .brand { left: 0; right: 0; top: 262px; justify-content: center; }
  .card-back .brand-name { font-size: 18px; }

  .contact {
    position: absolute;
    left: 40px; top: 28px;
    color: var(--white);
    font-size: 12px;
    line-height: 2;
  }
  .contact-row { display: flex; gap: 18px; }
  .contact-item { display: flex; align-items: center; gap: 7px; white-space: nowrap; }
  .contact-item svg { width: 13px; height: 13px; flex: none; }

  .person {
    position: absolute;
    left: 0; right: 0; top: 212px;
    text-align: center;
    color: var(--ink);
    font-size: 11px;
    letter-spacing: 1.5px;
  }
  .person .divider { margin: 0 8px; }
</style>
</head>
<body>

<section class="card card-front">
  <svg class="card-art" viewBox="0 0 620 354" preserveAspectRatio="none" aria-hidden="true">
    <defs>
      <linearGradient id="frontBand" x1="0" y1="0" x2="1" y2="0">
        <stop offset="0" stop-color="var(--blue)"/>
        <stop offset=".55" stop-color="var(--blue-light)"/>
        <stop offset="1" stop-color="var(--blue)"/>
      </linearGradient>
    </defs>
    <path d="M0 0 H620 V62 Q300 120 0 250 Z" fill="url(#frontBand)"/>
    <path d="M620 72 Q300 130 0 262" fill="none" stroke="var(--orange)" stroke-width="5"/>
  </svg>
  <p class="website">www.meadowlarkpetcare.com.au</p>
  <div class="brand">
    <span class="brand-dot"></span>
    <span class="brand-name">MEADOWLARK<br>PET CARE</span>
  </div>
</section>

<section class="card card-back">
  <svg class="card-art" viewBox="0 0 620 354" preserveAspectRatio="none" aria-hidden="true">
    <defs>
      <radialGradient id="backBand" cx=".5" cy=".7" r=".6">
        <stop offset="0" stop-color="var(--blue-light)"/>
        <stop offset="1" stop-color="var(--blue)"/>
      </radialGradient>
    </defs>
    <path d="M0 0 H620 V180 Q310 100 0 180 Z" fill="url(#backBand)"/>
    <path d="M620 190 Q310 110 0 190" fill="none" stroke="var(--orange)" stroke-width="5"/>
  </svg>

  <div class="contact">
    <div class="contact-row">
      <span class="contact-item">
        <svg viewBox="0 0 14 14"><circle cx="7" cy="7" r="7" fill="var(--white)"/><path d="M3.5 7.5 7 4.2l3.5 3.3V10.5h-7z" fill="var(--blue)"/></svg>
        Level 4, 18 Wattle St, VIC 3121
      </span>
      <span class="contact-item">
        <svg viewBox="0 0 14 14"><circle cx="7" cy="7" r="7" fill="var(--white)"/><circle cx="7" cy="7" r="4" fill="none" stroke="var(--blue)" stroke-width="1"/><path d="M3 7h8M7 3v8" stroke="var(--blue)" stroke-width="1"/></svg>
        www.meadowlarkpetcare.com.au
      </span>
    </div>
    <div class="contact-row">
      <span class="contact-item">
        <svg viewBox="0 0 14 14"><circle cx="7" cy="7" r="7" fill="var(--white)"/><path d="M4.5 3.5h2l.8 2-1.2.8a5 5 0 0 0 1.6 1.6l.8-1.2 2 .8v2c-3.8.3-6.3-2.2-6-6z" fill="var(--blue)"/></svg>
        0452 716 093
      </span>
      <span class="contact-item">
        <svg viewBox="0 0 14 14"><circle cx="7" cy="7" r="7" fill="var(--white)"/><rect x="4.8" y="3" width="4.4" height="8" rx="1" fill="var(--blue)"/></svg>
        03 9481 2275
      </span>
      <span class="contact-item">
        <svg viewBox="0 0 14 14"><circle cx="7" cy="7" r="7" fill="var(--white)"/><rect x="3.5" y="5" width="7" height="4.5" fill="var(--blue)"/><rect x="5" y="3" width="4" height="2" fill="var(--blue)"/></svg>
        03 9481 2276
      </span>
    </div>
    <div class="contact-row">
      <span class="contact-item">
        <svg viewBox="0 0 14 14"><circle cx="7" cy="7" r="7" fill="var(--white)"/><rect x="3.2" y="4.3" width="7.6" height="5.4" fill="var(--blue)"/><path d="M3.2 4.3 7 7.4l3.8-3.1" fill="none" stroke="var(--white)" stroke-width=".8"/></svg>
        dana@meadowlarkpetcare.com.au
      </span>
    </div>
  </div>

  <p class="person">DANA KOVICH<span class="divider">|</span>GENERAL MANAGER</p>

  <div class="brand">
    <span class="brand-dot"></span>
    <span class="brand-name">MEADOWLARK<br>PET CARE</span>
  </div>
</section>

</body>
</html>
```